Professional Website for Leading Global Private Equity Real Estate Company

The company is a leading global Private Equity Real Estate (PERE). We need a homepage design, an inner page design, and color/font tweaks to the logo (color should be more soothing than current blue used in the logo). The logo website should project the company as global, professional, experienced, trustworthy, accessible, YOUNG, DYNAMIC, hi-tech. PLEASE SEE the attached Design Brief Word Doc for details.

Target Market(s)

institional investors and wealthy private individuals

Industry/Entity Type

Finance

Number of Pages Required

2 page

Font styles to use
Sans Serif
Other font styles liked:
• either like in https://www.ferndalequay.com/ or like in presentations (Montserrat Black & Montserrat Light, Century Gothic, Blair ITC, Almoni Neue DL 4.0 AAA Medium, Almoni DL AAA)

Requirements
Must have
• new color palette that is NOT based on current logo. they want a more soothing color palette than the blue in that logo. the new color palette should project: global, professional, experienced, trustworthy, accessible, YOUNG, DYNAMIC, hi-tech.
Nice to have
• the likes these sites: https://www.ferndalequay.com/ and https://www.tvr.law/

```html
<!DOCTYPE html>
<html lang="en">
<head>
<meta charset="utf-8">
<title>Veltora Real Estate</title>
<link rel="stylesheet" href="https://fonts.googleapis.com/css2?family=Montserrat:wght@300;400;500;600;700;800&family=Oswald:wght@500;600&display=swap">
<style>
:root{
  --gold:#C79B3F;
  --gold-soft:#D9B46A;
  --ink:#1d1d1d;
  --text:#3a3a3a;
  --muted:#8a8a8a;
  --cream:#FBF6EC;
  --line:#d9d9d9;
  --dark:#262626;
  --white:#ffffff;
}
*{box-sizing:border-box;margin:0;padding:0}
html,body{width:1200px;height:4054px;overflow:hidden}
body{font-family:"Montserrat",sans-serif;color:var(--text);background:var(--white);position:relative}
.abs{position:absolute}
.gold{color:var(--gold)}
.btn{position:absolute;display:flex;align-items:center;gap:8px;background:var(--gold);color:var(--white);font-size:13px;font-weight:600;letter-spacing:.4px;border-radius:22px;padding:0 18px 0 12px;height:40px;text-transform:uppercase}
.btn .dot{width:20px;height:20px;border-radius:50%;background:rgba(255,255,255,.9)}
.brand{position:absolute;display:flex;align-items:center;gap:10px}
.brand .mark{width:46px;height:46px;border-radius:50%;background:var(--gold)}
.brand .name{font-weight:800;font-size:34px;letter-spacing:3px;color:var(--ink);line-height:1}
.brand .tag{font-size:13px;font-weight:600;letter-spacing:2px;color:var(--gold);margin-top:4px}
h2.title{position:absolute;font-size:34px;font-weight:700;color:var(--ink);letter-spacing:.3px}
p.body{font-size:12.3px;line-height:21px;color:var(--text);margin-bottom:10px}
.photo{position:absolute;border-radius:8px}

/* header / hero */
.hero{position:absolute;left:0;top:0;width:1200px;height:586px;background:linear-gradient(90deg,#ffffff 0%,#f8f3ea 30%,#d8c7b3 48%,#a7886e 62%,#6d5a4c 80%,#c7b5a0 100%)}
.hero .fade{position:absolute;inset:0;background:linear-gradient(90deg,rgba(255,255,255,.95) 0%,rgba(255,255,255,.75) 36%,rgba(255,255,255,0) 60%)}
.topbar{position:absolute;left:787px;top:14px;display:flex;gap:22px;font-size:14px;color:var(--ink);font-weight:500}
.topbar span{display:flex;align-items:center;gap:8px}
.ico-circle{width:26px;height:26px;border-radius:50%;background:var(--gold);display:flex;align-items:center;justify-content:center}
.topline{position:absolute;left:787px;top:52px;width:413px;height:1px;background:rgba(0,0,0,.25)}
.nav{position:absolute;left:490px;top:74px;display:flex;gap:33px;font-size:14px;color:var(--ink);font-weight:500}
.hero h1{position:absolute;left:164px;top:240px;font-family:"Oswald",sans-serif;font-weight:600;font-size:44px;line-height:53px;color:var(--ink)}

/* about */
.about-text{position:absolute;left:164px;top:708px;width:410px}
.stat{position:absolute;width:198px;height:192px;background:var(--white);border-radius:12px;box-shadow:0 6px 28px rgba(0,0,0,.08);text-align:center;padding-top:24px}
.stat .num{font-size:34px;font-weight:700;color:var(--gold);margin-top:8px;line-height:40px}
.stat .unit{font-size:22px;font-weight:500;color:var(--gold);line-height:30px}
.stat .lbl{font-size:13px;font-weight:600;color:var(--ink);margin-top:8px}

/* platforms */
.platforms{position:absolute;left:0;top:1181px;width:1200px;height:709px;background:var(--cream)}
.tab{position:absolute;left:164px;width:222px;height:58px;background:var(--white);border:1px solid #eadfcb;display:flex;align-items:center;gap:10px;padding-left:18px}
.tab .mark{width:38px;height:38px;border-radius:50%;background:var(--gold)}
.tab .nm{font-weight:800;font-size:20px;letter-spacing:2px;color:var(--ink);line-height:1}
.tab .sub{font-size:12px;letter-spacing:1.2px;color:var(--gold);margin-top:3px}
.tab.active{background:var(--gold);border-color:var(--gold)}
.tab.active .mark{background:var(--white)}
.tab.active .nm,.tab.active .sub{color:var(--white)}
.tab.active::after{content:"";position:absolute;right:-14px;top:15px;border-left:14px solid var(--gold);border-top:14px solid transparent;border-bottom:14px solid transparent}

/* newsletter */
.newsletter{position:absolute;left:161px;top:2350px;width:878px;height:288px;background:var(--white);border-radius:10px;box-shadow:0 4px 30px rgba(0,0,0,.07);overflow:hidden}
.newsletter .arc{position:absolute;right:-60px;bottom:-90px;width:300px;height:300px;border-radius:50%;background:#f7f1e6}
.field-email{position:absolute;left:233px;top:170px;width:412px;height:42px;border:1px solid #c9c9c9;border-radius:22px;font-size:11px;color:var(--muted);padding:13px 24px}
.field-email .go{position:absolute;right:3px;top:3px;width:62px;height:34px;border-radius:18px;background:var(--gold);display:flex;align-items:center;justify-content:center}

/* contact */
.contact{position:absolute;left:0;top:3087px;width:1200px;height:551px;background:linear-gradient(180deg,#ffffff 0%,#ffffff 55%,#eef0f3 78%,#b9bec6 100%)}
.field{position:absolute;width:221px;border-bottom:1px solid #bdbdbd;height:46px}
.field label{display:block;font-size:12.5px;font-weight:600;color:var(--ink)}
.field span{display:block;font-size:12px;color:var(--muted);margin-top:6px}

/* footer */
.footer{position:absolute;left:0;top:3638px;width:1200px;height:370px;background:var(--dark);color:#e6e6e6;overflow:hidden}
.footer .arc{position:absolute;right:-120px;top:-60px;width:420px;height:420px;border-radius:50%;border:70px solid #2f2f2f}
.fcol{position:absolute;top:96px}
.fcol h4{font-size:16px;font-weight:500;color:var(--white);margin-bottom:22px}
.fcol li{list-style:none;font-size:13px;line-height:30px}
.contact-row{display:flex;gap:14px;margin-bottom:14px}
.contact-row b{display:block;font-size:13px;font-weight:600;color:var(--white)}
.contact-row span{font-size:13px}
.copy{position:absolute;left:0;top:4008px;width:1200px;height:46px;background:var(--gold);color:var(--white);font-size:12.5px}
.social{position:absolute;display:flex;gap:8px;left:943px;top:10px}
.social i{width:26px;height:26px;border-radius:50%;border:1.5px solid var(--white);display:block}
</style>
</head>
<body>

<!-- Header & hero -->
<section class="hero">
  <div role="img" aria-label="Photo of two business colleagues giving a high five at an office desk" class="abs" style="left:500px;top:0;width:700px;height:586px;background:linear-gradient(100deg,rgba(0,0,0,0) 0%,rgba(120,95,75,.35) 40%,rgba(70,60,55,.5) 70%,rgba(190,170,150,.3) 100%)"></div>
  <div class="fade"></div>
  <div class="brand" style="left:164px;top:18px">
    <div class="mark"></div>
    <div><div class="name">VELTORA</div><div class="tag">REAL ESTATE</div></div>
  </div>
  <div class="topbar">
    <span><i class="ico-circle"><svg width="14" height="10" viewBox="0 0 14 10"><rect x=".7" y=".7" width="12.6" height="8.6" rx="1" fill="none" stroke="#fff" stroke-width="1.3"/><path d="M1 1l6 5 6-5" fill="none" stroke="#fff" stroke-width="1.3"/></svg></i>info@veltora.com</span>
    <span><i class="ico-circle"><svg width="12" height="13" viewBox="0 0 12 13"><circle cx="6" cy="4" r="3" fill="none" stroke="#fff" stroke-width="1.3"/><path d="M1 12.5c0-3 2.2-4.5 5-4.5s5 1.5 5 4.5" fill="none" stroke="#fff" stroke-width="1.3"/></svg></i>Login</span>
  </div>
  <div class="topline"></div>
  <nav class="nav"><span>Home</span><span>About Us</span><span>Our Businesses</span><span>Investors</span><span>News</span><span>Contact Us</span></nav>
  <h1>We Are Leading<br>Global Private Equity<br>Real Estate Firm</h1>
  <div class="btn" style="left:162px;top:416px"><i class="dot"></i>About Us</div>
</section>

<!-- About -->
<section>
  <div class="abs" style="left:760px;top:620px;width:470px;height:470px;border-radius:50%;background:#faf6ee"></div>
  <h2 class="title" style="left:164px;top:658px">About <span class="gold">Us</span></h2>
  <div class="about-text">
    <p class="body">Veltora Consumer Products, of the Norvan Group, which was founded in 1951, is the longest-standing and leading company in Israel in the area of home electrical appliances and air conditioning.</p>
    <p class="body">The Company is engaged in the production, import, export, sales, distribution, marketing and provision of services for a broad variety of consumer electrical appliances.</p>
    <p class="body">The Company has an annual sales turnover of NIS 2.49 billion and it employs around 1,600 employees.</p>
    <p class="body">The Company owns two chains specializing in the sale of some of the leading electric products in Israel: Halden Electric and Brightway Stores.</p>
    <p class="body">Veltora sells and markets a variety of leading products and brands, ranging from the affordable to luxury brands.</p>
  </div>
  <div class="btn" style="left:162px;top:1040px"><i class="dot"></i>Read More</div>

  <div class="stat" style="left:619px;top:663px">
    <svg width="36" height="36" viewBox="0 0 36 36" fill="none" stroke="#333" stroke-width="1.4"><circle cx="16" cy="18" r="9"/><path d="M16 13v10M13.5 15.5h4a1.8 1.8 0 010 3.5h-3a1.8 1.8 0 000 3.5h4"/><path d="M12 8l4-4 4 4"/><rect x="24" y="22" width="9" height="10"/></svg>
    <div class="num">4.6</div><div class="unit">NIS Bilion</div><div class="lbl">Annual Revenues</div>
  </div>
  <div class="stat" style="left:841px;top:695px">
    <svg width="36" height="36" viewBox="0 0 36 36" fill="none" stroke="#333" stroke-width="1.4"><circle cx="11" cy="10" r="6"/><circle cx="25" cy="10" r="6"/><path d="M18 16v16M11 16c0 6 7 6 7 10M25 16c0 6-7 6-7 10"/></svg>
    <div class="num">265.59</div><div class="unit">NIS Million</div><div class="lbl">Annual Operating Income</div>
  </div>
  <div class="stat" style="left:619px;top:877px">
    <svg width="36" height="36" viewBox="0 0 36 36" fill="none" stroke="#333" stroke-width="1.4"><circle cx="19" cy="10" r="6"/><path d="M4 26l6-4h8l6 2 8-6M4 32l8-3h10l10-7"/></svg>
    <div class="num">164</div><div class="unit">NIS Million</div><div class="lbl">Annual Net Profit</div>
  </div>
  <div class="stat" style="left:841px;top:909px">
    <svg width="36" height="36" viewBox="0 0 36 36" fill="none" stroke="#333" stroke-width="1.4"><path d="M20 6l8 6v10h-16V12z"/><path d="M17 19l6-6"/><circle cx="18" cy="14" r="1"/><circle cx="22" cy="18" r="1"/><path d="M4 28l6-4h8l6 2M4 33l8-3h12"/></svg>
    <div class="num">1.2</div><div class="unit">NIS Bilion</div><div class="lbl">Equity</div>
  </div>
</section>

<!-- Investment platforms -->
<section class="platforms">
  <h2 class="title" style="left:0;width:1200px;text-align:center;top:72px">Our Investment <span class="gold">Platforms</span></h2>
  <div class="tab" style="top:151px"><i class="mark"></i><div><div class="nm">VELTORA</div><div class="sub">MULTIFAMILY</div></div></div>
  <div class="tab active" style="top:225px"><i class="mark"></i><div><div class="nm">VELTORA</div><div class="sub">DEBT</div></div></div>
  <div class="tab" style="top:299px"><i class="mark"></i><div><div class="nm">VELTORA</div><div class="sub">SINGLE FAMILY</div></div></div>
  <div class="tab" style="top:373px"><i class="mark"></i><div><div class="nm">VELTORA</div><div class="sub">HOSPITALITY</div></div></div>
  <div class="tab" style="top:447px"><i class="mark"></i><div><div class="nm">VELTORA</div><div class="sub">UK</div></div></div>
  <div role="img" aria-label="Photo of hands reviewing financial charts beside a laptop" class="photo" style="left:484px;top:151px;width:555px;height:240px;background:linear-gradient(135deg,#6f7a80 0%,#c9ccc9 45%,#e3e2dc 60%,#8a8f90 100%)"></div>
  <div class="abs" style="left:486px;top:415px;font-size:23px;font-weight:700;color:var(--ink)">Veltora Debt</div>
  <div class="abs" style="left:486px;top:454px;width:553px">
    <p class="body" style="font-size:12.8px;line-height:24px">Lorem ipsum dolor sit amet, consectetuer adipiscing elit, sed diam nonummy nibh euismod tincidunt ut laoreet dolore magna aliquam erat volutpat.</p>
    <p class="body" style="font-size:12.8px;line-height:24px">Duis autem vel eum iriure dolor in hendrerit in vulputate velit esse molestie conseq vel illum dolore eu feugiat nulla facilisis at vero eros et accumsan et iusto odio digni qui blandit praesent luptatum zzril delenit augue duis.</p>
  </div>
  <div class="btn" style="left:484px;top:590px"><i class="dot"></i>Contact Us</div>
</section>

<!-- Our Edge -->
<section>
  <div role="img" aria-label="Photo of two businessmen reviewing documents in a bright office lounge" class="photo" style="left:164px;top:1969px;width:417px;height:299px;background:linear-gradient(135deg,#c4c9cc 0%,#8f9aa3 40%,#3f4a5a 65%,#b8bec2 100%)"></div>
  <h2 class="title" style="left:627px;top:1980px">Our <span class="gold">Edge</span></h2>
  <div class="abs" style="left:627px;top:2034px;width:412px">
    <p class="body" style="font-size:11.5px">Lorem ipsum dolor sit amet, consectetuer adipiscing elit, sed diam nonummy nibh euismod tincidunt ut laoreet dolore magna aliquam erat volutpat.</p>
    <p class="body" style="font-size:11.5px">Lorem ipsum dolor sit amet, consectetuer adipiscing elit, sed diam nonummy</p>
    <p class="body" style="font-size:11.5px">Lorem ipsum dolor sit amet, consectetuer adipiscing elit, sed diam nonummy</p>
  </div>
  <div class="btn" style="left:626px;top:2208px"><i class="dot"></i>Investor Information</div>
</section>

<!-- Newsletter -->
<section class="newsletter">
  <div class="arc"></div>
  <svg class="abs" style="left:622px;top:32px" width="44" height="38" viewBox="0 0 44 38"><path d="M2 20L42 2 30 36 20 24z" fill="var(--gold-soft)"/><path d="M20 24L42 2 16 30z" fill="var(--gold)"/></svg>
  <h2 class="title" style="left:0;width:878px;text-align:center;top:70px">Newsletter <span class="gold">Signup</span></h2>
  <div class="abs" style="left:0;width:878px;text-align:center;top:128px;font-size:13px;color:var(--text)">Lorem ipsum dolor sit amet, consectetuer adipiscing elit, sed diam nonummy</div>
  <div class="field-email">Enter email id<span class="go"><svg width="10" height="14" viewBox="0 0 10 14"><path d="M2 2l5 5-5 5" fill="none" stroke="#fff" stroke-width="2"/></svg></span></div>
</section>

<!-- Responsibility -->
<section>
  <h2 class="title" style="left:164px;top:2740px">Our <span class="gold">Responsibility</span></h2>
  <div class="abs" style="left:164px;top:2792px;width:412px">
    <p class="body" style="font-size:11.5px">Lorem ipsum dolor sit amet, consectetuer adipiscing elit, sed diam nonummy nibh euismod tincidunt ut laoreet dolore magna aliquam erat volutpat.</p>
    <p class="body" style="font-size:11.5px">Lorem ipsum dolor sit amet, consectetuer adipiscing elit, sed diam nonummy</p>
    <p class="body" style="font-size:11.5px">Lorem ipsum dolor sit amet, consectetuer adipiscing elit, sed diam nonummy</p>
  </div>
  <div class="btn" style="left:162px;top:2966px"><i class="dot"></i>Read More</div>
  <div role="img" aria-label="Photo of two businessmen shaking hands" class="photo" style="left:619px;top:2726px;width:420px;height:299px;background:linear-gradient(135deg,#eceef0 0%,#c9cdd1 50%,#a8adb3 100%)"></div>
</section>

<!-- Contact -->
<section class="contact">
  <div role="img" aria-label="Misty city skyline with towers" class="abs" style="left:0;top:340px;width:1200px;height:211px;background:linear-gradient(180deg,rgba(160,168,178,0) 0%,rgba(120,128,140,.45) 60%,rgba(80,88,100,.7) 100%)"></div>
  <div class="abs" style="left:164px;top:130px;font-size:30px;font-weight:700;color:var(--ink);line-height:40px">Ready To Join<br>Veltora Real Estate</div>
  <div class="abs" style="left:164px;top:216px;width:260px;font-size:13px;line-height:24px">Fill the form and find opportunities to join blank convas lorem ipsum yet amet.</div>
  <svg class="abs" style="left:162px;top:309px" width="26" height="26" viewBox="0 0 24 24"><path d="M5 2h4l2 5-3 2a12 12 0 006 6l2-3 5 2v4a2 2 0 01-2 2A18 18 0 013 4a2 2 0 012-2z" fill="none" stroke="var(--gold)" stroke-width="1.8"/></svg>
  <div class="abs" style="left:204px;top:296px;font-size:18px;font-weight:500;color:var(--ink);line-height:26px">Call Us<br><b style="font-weight:700">+987 654 0198</b></div>

  <div class="field" style="left:528px;top:68px"><label>First Name</label><span>John</span></div>
  <div class="field" style="left:797px;top:68px"><label>Last Name</label><span>Smith</span></div>
  <div class="field" style="left:528px;top:156px"><label>Phone</label><span>123 456 7890</span></div>
  <div class="field" style="left:797px;top:156px"><label>Email</label><span>johnsmith@gmail.com</span></div>
  <div class="field" style="left:528px;top:254px;width:490px;height:132px"><label>Message</label><span>Type your message here</span></div>
  <div class="abs" style="left:960px;top:337px;width:60px;height:60px;border-radius:50%;background:var(--gold);display:flex;align-items:center;justify-content:center"><svg width="26" height="26" viewBox="0 0 24 24"><path d="M2 12L22 3l-6 18-4-7z" fill="#fff"/></svg></div>
</section>

<!-- Footer -->
<footer class="footer">
  <div class="arc"></div>
  <div class="brand" style="left:164px;top:88px">
    <div class="mark" style="width:34px;height:34px"></div>
    <div><div class="name" style="color:var(--white);font-size:26px">VELTORA</div><div class="tag" style="font-size:10px">REAL ESTATE</div></div>
  </div>
  <div class="abs" style="left:164px;top:150px;width:240px;font-size:13px;line-height:25px">Lorem ipsum dolor sit amet sfbuy consectetuer adipiscing elit, sedti diam nonummy nibh euismodrtt tincidunt ut laoreet dolore magn aliquam erat volutpat.</div>
  <div class="fcol" style="left:443px"><h4>Quick <span class="gold">Links</span></h4><ul><li>Home</li><li>About Us</li><li>Our Businesses</li><li>Investors</li><li>News</li><li>Contact Us</li></ul></div>
  <div class="fcol" style="left:606px"><h4>Our <span class="gold">Businesses</span></h4><ul><li>Veltora Multifamily</li><li>Veltora Debt</li><li>Veltora Single Family</li><li>Veltora Hospitality</li><li>Veltora UK</li></ul></div>
  <div class="fcol" style="left:808px"><h4>Contact <span class="gold">Details</span></h4>
    <div class="contact-row"><svg width="14" height="20" viewBox="0 0 14 20"><path d="M7 0a7 7 0 017 7c0 5-7 13-7 13S0 12 0 7a7 7 0 017-7z" fill="var(--gold)"/><circle cx="7" cy="7" r="2.5" fill="var(--dark)"/></svg><div><b>Address</b><span>Street Name, City - 987 654</span></div></div>
    <div class="contact-row"><svg width="14" height="16" viewBox="0 0 24 24"><path d="M5 2h4l2 5-3 2a12 12 0 006 6l2-3 5 2v4a2 2 0 01-2 2A18 18 0 013 4a2 2 0 012-2z" fill="var(--gold)"/></svg><div><b>Phone</b><span>+987 654 0198</span></div></div>
    <div class="contact-row"><svg width="16" height="12" viewBox="0 0 16 12"><rect width="16" height="12" rx="1" fill="var(--gold)"/><path d="M1 1l7 6 7-6" fill="none" stroke="var(--dark)" stroke-width="1.3"/></svg><div><b>Email</b><span>info@veltora.com</span></div></div>
  </div>
</footer>
<div class="copy">
  <div class="abs" style="left:164px;top:15px">Copyright © 2022 Veltora. All Rights Reserved.</div>
  <div class="social"><i></i><i></i><i></i></div>
</div>

</body>
</html>
```